Podcast Cover Art for rebranded podcast - I have inspiration for the designs

I've had a podcast ("Paperboat Radio Hour") since 2018, but I'm in the process of rebranding it. I've attached the old cover art below, which I loved, but I don't need it to look like that at all. The rebranded podcast is called 'Open Window with Marnie Cole.' I've included the show description at the bottom. I've been working on various design options in Canva, but not obsessed with anything yet, but I'm attaching the ones I do like that I think just need some refining. My very favorite is the one labeled 'favorite_Open Window' so I wouldn't mind keeping that general idea but perfected by a designer. Ultimately, I want something cool, fairly clean, modern, eye catching. I'm into neutrals with maybe a pop of color, so think black, white, grey..maybe silver, and I love a pop of red..and I'm not opposed to other options for the pop color. The show is going to be inspiring, entertaining, and funny. Oh and one other idea I had but I'm not sure if it makes sense with the title and/or what the show is about..but a vinyl record with Open Window with Marnie Cole on it somehow, on a record player..not sure.

Ever wonder what it means to truly live authentically? Curious about how to embrace the unpredictability of life? Ready for some heartfelt and lighthearted conversations that inspire and entertain?
Join Marnie Cole as she dives into the raw, real, and unscripted moments of life. In each episode, Marnie brings candid conversations and genuine insights into the ups and downs we all experience. From personal growth and self-discovery to inspiring stories and valuable life lessons, "Open Window" is a space where authenticity reigns and spontaneity is celebrated.
Whether she's sharing her own journey or chatting with inspiring guests, Marnie invites you to explore the beauty of living life without a script. Expect honest reflections, thought-provoking discussions, and a refreshing perspective on navigating life's unpredictable path—all with a dash of fun and humor to keep things lively and entertaining. Step into the unscripted moments of life and tune in for a blend of depth and lightheartedness that will leave you inspired, smiling, and most importantly laughing.

Target Market(s)

25-50 year old women and men (primarily women)

Font styles to use
Sans Serif

Requirements
Should not have
• nothing too feminine or girly, nothing cheesy :)

```html
<!DOCTYPE html>
<html lang="en">
<head>
<meta charset="utf-8">
<title>Open Window with Marnie Cole – Podcast Cover</title>
<link rel="stylesheet" href="https://fonts.googleapis.com/css2?family=Anton&family=Allura&display=swap">
<style>
  :root {
    --bg-light: #f1f3df;
    --bg-mid: #dfe4c8;
    --bg-deep: #cfd6b6;
    --sage: #7fa07a;
    --sage-soft: #a9c0a0;
    --forest: #214d18;
    --ink-outline: #1c2a35;
    --white: #ffffff;
    --photo-warm: #b99478;
    --photo-dark: #2f332c;
  }
  * { margin: 0; padding: 0; box-sizing: border-box; }
  html, body { width: 1200px; height: 1200px; overflow: hidden; background: var(--bg-light); }

  .cover {
    position: relative;
    width: 1200px;
    height: 1200px;
    overflow: hidden;
    background: radial-gradient(ellipse at 40% 20%, var(--bg-light) 0%, var(--bg-mid) 60%, var(--bg-deep) 100%);
  }

  .backdrop-portrait {
    position: absolute;
    left: 330px; top: 230px;
    width: 520px; height: 970px;
    background: linear-gradient(180deg, rgba(160,170,140,0.18), rgba(120,130,105,0.28));
    border-radius: 260px 260px 0 0;
  }

  .host-photo {
    position: absolute;
    left: 700px; top: 160px;
    width: 480px; height: 1040px;
    background: linear-gradient(170deg, var(--photo-warm) 0%, #6b4a36 35%, var(--photo-dark) 65%, #1f2320 100%);
    border-radius: 200px 200px 0 0;
    opacity: 0.9;
  }
  .host-photo-outline {
    position: absolute;
    left: 688px; top: 148px;
    width: 504px; height: 1060px;
    border: 2px solid var(--forest);
    border-radius: 212px 212px 0 0;
  }

  .title-top {
    position: absolute;
    left: 74px; top: 130px;
    font-family: "Anton", sans-serif;
    font-size: 340px;
    line-height: 1;
    letter-spacing: 4px;
    color: var(--sage);
    -webkit-text-stroke: 3px var(--ink-outline);
    text-shadow: inset 0 0 0 transparent;
  }
  .title-bottom {
    position: absolute;
    left: 66px; top: 475px;
    font-family: "Anton", sans-serif;
    font-size: 172px;
    line-height: 1;
    letter-spacing: 2px;
    color: var(--forest);
  }

  .mic-graphic {
    position: absolute;
    left: 520px; top: 690px;
    width: 220px; height: 250px;
  }

  .with-word {
    position: absolute;
    left: 100px; top: 730px;
    font-family: "Allura", cursive;
    font-size: 190px;
    line-height: 1;
    color: var(--sage);
  }

  .host-name {
    position: absolute;
    left: 100px; top: 900px;
    width: 618px; height: 148px;
    background: var(--forest);
    display: flex;
    align-items: center;
    justify-content: center;
    font-family: "Anton", sans-serif;
    font-size: 108px;
    line-height: 1;
    color: var(--white);
    letter-spacing: 1px;
  }
</style>
</head>
<body>
  <main class="cover">
    <div class="backdrop-portrait" role="img" aria-label="Faded background portrait photo of the host, tinted pale green"></div>
    <div class="host-photo" role="img" aria-label="Photo of the host dancing with arms raised, long dark hair, dark t-shirt and sequinned shorts"></div>
    <div class="host-photo-outline"></div>

    <h1 class="title">
      <span class="title-top">OPEN</span>
      <span class="title-bottom">WINDOW</span>
    </h1>

    <svg class="mic-graphic" viewBox="0 0 220 250" role="img" aria-label="Illustration of a handheld microphone with cable">
      <defs>
        <linearGradient id="micTone" x1="0" y1="0" x2="1" y2="1">
          <stop offset="0" stop-color="#2d5a24" stop-opacity="0.55"/>
          <stop offset="1" stop-color="#214d18" stop-opacity="0.35"/>
        </linearGradient>
      </defs>
      <rect x="0" y="0" width="220" height="250" rx="20" fill="url(#micTone)"/>
    </svg>

    <span class="with-word">with</span>
    <div class="host-name">Marnie Cole</div>
  </main>
</body>
</html>
```